Health Care Company with Logo Needs Business Cards designed

We are a luxury behavioral health company looking for business cards design we already have a logo and are looking for someone to design a sophisticated luxurious looking business card. Please note that Card design should be captivating just like the logo and also encompass the logo color

Industry/Entity Type

Healthcare

Contact Information for Business Card

Logo,company name, tagline, my name and title, contact details, and physical address

```html
<!DOCTYPE html>
<html lang="en">
<head>
<meta charset="UTF-8">
<title>Corvane Behavioral Health — Business Card</title>
<link href="https://fonts.googleapis.com/css2?family=Roboto+Condensed:wght@700&family=Roboto:ital,wght@0,400;0,500;1,400&display=swap" rel="stylesheet">
<style>
  :root {
    --backdrop: #2a2a2a;
    --card-dark: #1a1a1b;
    --card-dark-sheen: #3a3a3c;
    --card-dark-deep: #0c0c0d;
    --card-light: #f2f2f2;
    --brand-purple: #7b2f8e;
    --brand-blue: #1a8fd0;
    --brand-orange: #ea8a12;
    --brand-green: #8cba2e;
    --ink: #2a2a2a;
  }
  * { margin: 0; padding: 0; box-sizing: border-box; }
  html, body { width: 1138px; height: 1200px; overflow: hidden; }
  body { background: var(--backdrop); position: relative; font-family: "Roboto", sans-serif; }

  .card { position: absolute; border-radius: 16px; overflow: hidden; }

  .card-back {
    left: 186px; top: 302px; width: 376px; height: 624px;
    background: var(--card-dark);
  }
  .card-back .pattern-field {
    position: absolute; inset: 0;
    background:
      radial-gradient(ellipse 70% 45% at 25% 12%, rgba(150,150,155,0.32), transparent 70%),
      radial-gradient(ellipse 60% 40% at 80% 85%, rgba(0,0,0,0.55), transparent 75%),
      linear-gradient(165deg, var(--card-dark-sheen) 0%, var(--card-dark) 45%, var(--card-dark-deep) 100%);
  }
  .card-back .back-mark {
    position: absolute; left: 0; right: 0; top: 358px;
    display: flex; align-items: center; justify-content: center; gap: 10px;
  }
  .back-mark .mark-dot { width: 14px; height: 14px; border-radius: 50%; background: var(--brand-orange); }
  .back-mark .mark-name {
    font-family: "Roboto Condensed", sans-serif; font-weight: 700;
    font-size: 26px; color: var(--brand-orange); letter-spacing: 1px;
  }

  .card-front {
    left: 608px; top: 306px; width: 374px; height: 618px;
    background: var(--card-light);
    text-align: center;
  }
  .brand-block { position: absolute; left: 0; right: 0; top: 106px; }
  .brand-block .brand-dot {
    width: 64px; height: 64px; border-radius: 50%; background: var(--brand-purple);
    margin: 0 auto 44px;
  }
  .brand-name {
    font-family: "Roboto Condensed", sans-serif; font-weight: 700;
    font-size: 26px; color: var(--brand-purple); line-height: 1;
  }
  .brand-tagline {
    margin-top: 6px;
    font-family: "Roboto", sans-serif; font-weight: 500;
    font-size: 8.5px; letter-spacing: 2px; color: var(--brand-blue);
  }
  .person { position: absolute; left: 0; right: 0; top: 318px; }
  .person-name { font-weight: 500; font-size: 22px; color: var(--brand-blue); letter-spacing: 0.3px; }
  .person-title { margin-top: 4px; font-style: italic; font-size: 15px; color: var(--ink); }

  .contact-divider {
    position: absolute; left: 0; right: 0; top: 396px;
    display: flex; align-items: center; justify-content: center; gap: 4px;
  }
  .contact-divider .rule { width: 78px; height: 2px; }
  .rule-left { background: linear-gradient(90deg, transparent, var(--brand-purple)); margin-right: 10px; }
  .rule-right { background: linear-gradient(90deg, var(--brand-blue), transparent); margin-left: 10px; }

  .contact-list { position: absolute; left: 0; right: 0; top: 437px; font-size: 14.5px; color: var(--ink); line-height: 22px; }
  .address { margin-top: 19px; }
</style>
</head>
<body>
  <div class="card card-back">
    <div class="pattern-field" role="img" aria-label="Embossed tone-on-tone brand pattern on glossy dark stock"></div>
    <div class="back-mark">
      <span class="mark-dot"></span>
      <span class="mark-name">Corvane</span>
    </div>
  </div>

  <div class="card card-front">
    <div class="brand-block">
      <div class="brand-dot"></div>
      <div class="brand-name">Corvane Behavioral Health</div>
      <div class="brand-tagline">DEDICATED TO HOPE, HEALING AND RECOVERY</div>
    </div>

    <div class="person">
      <div class="person-name">DANIEL REYES</div>
      <div class="person-title">Managing Director</div>
    </div>

    <div class="contact-divider">
      <span class="rule rule-left"></span>
      <svg width="26" height="26" viewBox="0 0 26 26" aria-label="Phone">
        <circle cx="13" cy="13" r="11.5" fill="none" stroke="var(--brand-purple)" stroke-width="1.6"/>
        <circle cx="13" cy="13" r="9" fill="var(--brand-blue)"/>
        <path d="M8.5 11.5c0-1.5 2-2.5 4.5-2.5s4.5 1 4.5 2.5l-1.6.4-.5-1.3h-4.8l-.5 1.3zM10 12.5h6l1 4h-8z" fill="#fff"/>
      </svg>
      <svg width="26" height="26" viewBox="0 0 26 26" aria-label="Email">
        <circle cx="13" cy="13" r="11.5" fill="none" stroke="var(--brand-purple)" stroke-width="1.6"/>
        <circle cx="13" cy="13" r="9" fill="var(--brand-blue)"/>
        <rect x="7.5" y="9.5" width="11" height="7.5" fill="#fff"/>
        <path d="M7.5 9.5l5.5 4.5 5.5-4.5" fill="none" stroke="var(--brand-blue)" stroke-width="1"/>
      </svg>
      <svg width="26" height="26" viewBox="0 0 26 26" aria-label="Website">
        <circle cx="13" cy="13" r="11.5" fill="none" stroke="var(--brand-purple)" stroke-width="1.6"/>
        <circle cx="13" cy="13" r="9" fill="var(--brand-blue)"/>
        <g fill="none" stroke="#fff" stroke-width="1">
          <circle cx="13" cy="13" r="5.5"/>
          <ellipse cx="13" cy="13" rx="2.4" ry="5.5"/>
          <path d="M7.5 13h11M8.3 10.3h9.4M8.3 15.7h9.4"/>
        </g>
      </svg>
      <span class="rule rule-right"></span>
    </div>

    <div class="contact-list">
      <div>555-204-7391</div>
      <div>daniel@corvanehealth.com</div>
      <div>www.corvanehealth.com</div>
      <div class="address">48, Linden Row, Marlow Bay,<br>Harbor Vale, US 940172</div>
    </div>
  </div>
</body>
</html>
```